Homemaking training schools needs a Business Card design

Designer, Hello!

No special requirements, good-looking enough.
--------------------------------------------------------------------------

Name: Marcus Dole
Chairman
Tel: 0574-71948263
Mobile: 13857420916
Email: kelvora@mailnest.example
Web: www.prt2019.example
Add: No.258, LanpingJie, BeiyuanQu, Ningbo, Zhejiang

LOGO
Ningbo PRT Homemaking Training School

Target Market(s)

pregnant women, mothers, infants, the elderly and families, including cleaning, cooking, nursing training.

Industry/Entity Type

Business

Contact Information for Business Card

Name: Marcus Dole
Chairman
Tel: 0574-71948263
Mobile: 13857420916
Email: kelvora@mailnest.example
Web: www.prt2019.example

LOGO

Font styles to use
Serif
Sans Serif
Decorative

Requirements
Nice to have
• Feels: clean, specifications, safety, comfort, warmth and happiness.

```html
<!DOCTYPE html>
<html lang="en">
<head>
<meta charset="utf-8">
<title>PeiRenTang Business Card</title>
<link rel="stylesheet" href="https://fonts.googleapis.com/css2?family=Montserrat:wght@400;500;600;700;800&display=swap">
<style>
  :root {
    --brand-blue: #1b75bc;
    --brand-pink: #e6007e;
    --ink-gray: #555555;
    --card-white: #ffffff;
    --backdrop: #2b2b2d;
  }
  * { margin: 0; padding: 0; box-sizing: border-box; }
  html, body {
    width: 1200px; height: 900px; overflow: hidden;
    background: var(--backdrop);
    font-family: "Montserrat", sans-serif;
  }
  .stage {
    position: relative; width: 1200px; height: 900px;
  }
  .card {
    position: absolute; left: 240px; width: 720px; height: 410px;
    background: var(--card-white); overflow: hidden;
  }
  .card--front { top: 30px; }
  .card--back { top: 460px; }

  .brand {
    position: absolute; left: 0; right: 0;
    display: flex; align-items: center; justify-content: center; gap: 14px;
  }
  .brand__dot {
    width: 22px; height: 22px; border-radius: 50%;
    background: var(--brand-pink);
  }
  .brand__name {
    font-weight: 700; font-size: 58px; letter-spacing: -1px;
    color: var(--brand-blue); line-height: 1;
  }
  .card--front .brand { top: 150px; }
  .card--front .rule {
    position: absolute; top: 232px; height: 2px; background: var(--ink-gray);
  }
  .card--front .rule--left { left: 150px; width: 170px; }
  .card--front .rule--right { left: 400px; width: 170px; }
  .web-link {
    position: absolute; top: 300px; left: 0; right: 0; text-align: center;
    font-weight: 700; font-size: 19px; color: var(--brand-blue);
  }

  .card--back .brand { top: 70px; }
  .card--back .brand__name { font-size: 50px; }
  .card--back .rule {
    position: absolute; height: 2px;
  }
  .card--back .rule--left { top: 170px; left: 160px; width: 180px; background: var(--ink-gray); }
  .card--back .rule--right { top: 170px; left: 380px; width: 180px; background: var(--ink-gray); }
  .band-edge {
    position: absolute; left: 0; right: 0; top: 222px; height: 3px;
    background: var(--brand-blue);
  }
  .band {
    position: absolute; left: 0; right: 0; top: 230px; bottom: 0;
    background: var(--brand-pink); color: var(--card-white);
  }
  .holder {
    position: absolute; left: 48px; top: 34px;
  }
  .holder__name {
    font-weight: 800; font-size: 32px; letter-spacing: 1px; line-height: 1;
  }
  .holder__role {
    font-weight: 500; font-size: 14px; letter-spacing: 1px; margin-top: 6px;
    text-align: right;
  }
  .holder__address {
    font-weight: 500; font-size: 15px; line-height: 1.45; margin-top: 14px;
  }
  .contacts {
    position: absolute; left: 420px; top: 30px; list-style: none;
  }
  .contacts__item {
    display: flex; align-items: center; gap: 10px;
    font-weight: 600; font-size: 16px; line-height: 1; margin-bottom: 13px;
  }
  .contacts__icon { width: 15px; height: 15px; flex: none; }
</style>
</head>
<body>
<main class="stage">

  <section class="card card--front" aria-label="Business card front">
    <div class="brand">
      <span class="brand__dot"></span>
      <span class="brand__name">PeiRenTang</span>
    </div>
    <span class="rule rule--left"></span>
    <span class="rule rule--right"></span>
    <p class="web-link">www.prt2019.example</p>
  </section>

  <section class="card card--back" aria-label="Business card back">
    <div class="brand">
      <span class="brand__dot"></span>
      <span class="brand__name">PeiRenTang</span>
    </div>
    <span class="rule rule--left"></span>
    <span class="rule rule--right"></span>
    <span class="band-edge"></span>
    <div class="band">
      <div class="holder">
        <p class="holder__name">MARCUS DOLE</p>
        <p class="holder__role">CHAIRMAN</p>
        <p class="holder__address">258, LanpingJie<br>BeiyuanQu, Ningbo, Zhejiang</p>
      </div>
      <ul class="contacts">
        <li class="contacts__item">
          <svg class="contacts__icon" viewBox="0 0 16 16"><path d="M3 1l3 3-1.5 2a8 8 0 0 0 5.5 5.5L12 10l3 3-2 2C7 15 1 9 1 3z" fill="#fff"/></svg>
          0574-71948263
        </li>
        <li class="contacts__item">
          <svg class="contacts__icon" viewBox="0 0 16 16"><rect x="4" y="1" width="8" height="14" rx="1.5" fill="none" stroke="#fff" stroke-width="1.6"/><circle cx="8" cy="12.3" r="0.9" fill="#fff"/></svg>
          13857420916
        </li>
        <li class="contacts__item">
          <svg class="contacts__icon" viewBox="0 0 16 16"><rect x="1" y="3" width="14" height="10" fill="none" stroke="#fff" stroke-width="1.6"/><path d="M1 3l7 6 7-6" fill="none" stroke="#fff" stroke-width="1.6"/></svg>
          kelvora@mailnest.example
        </li>
        <li class="contacts__item">
          <svg class="contacts__icon" viewBox="0 0 16 16"><circle cx="8" cy="8" r="6.5" fill="none" stroke="#fff" stroke-width="1.5"/><ellipse cx="8" cy="8" rx="3" ry="6.5" fill="none" stroke="#fff" stroke-width="1.2"/><path d="M1.5 8h13" stroke="#fff" stroke-width="1.2"/></svg>
          www.prt2019.example
        </li>
      </ul>
    </div>
  </section>

</main>
</body>
</html>
```